Business Card Design for Occupational Medicine Start Up Company

We need to design a professional business card. We are a healthcare company providing occupational medicine services to blue collar industries. We are professional, efficient and high quality service providers.

Target Market(s)

Blue Collar Industry: Shipbuilding, Ports, Trucking Companies; The Executives and Safety Officers for these companies

Industry/Entity Type

Healthcare

Contact Information for Business Card

Logo, Name, Title, Email, Phone

Other font styles liked:
• Please match our Brand Guide

Requirements
Must have
• Our Company Colors and Logo

```html
<!DOCTYPE html>
<html lang="en">
<head>
<meta charset="utf-8">
<title>CrewWell Business Card</title>
<link href="https://fonts.googleapis.com/css2?family=Montserrat:wght@400;500;700&family=Oswald:wght@600&display=swap" rel="stylesheet">
<style>
  :root{
    --navy:#23308c;
    --sky:#2b9fdc;
    --amber:#f2a93b;
    --ink:#1f1f24;
    --card-black:#141416;
    --paper:#ffffff;
    --backdrop:#d2d1cd;
  }
  *{margin:0;padding:0;box-sizing:border-box}
  html,body{width:1200px;height:801px;overflow:hidden}
  body{
    background:var(--backdrop);
    font-family:"Montserrat",sans-serif;
    position:relative;
  }
  .card{
    position:absolute;
    width:525px;height:300px;
    border-radius:3px;
    box-shadow:0 14px 30px rgba(0,0,0,.22);
    overflow:hidden;
  }
  .card--front{left:50px;top:250px;background:var(--paper);border-bottom:3px solid var(--amber)}
  .card--back{left:625px;top:250px;background:var(--card-black);border-bottom:3px solid var(--amber)}

  .brand{
    position:absolute;left:56px;top:70px;
    display:flex;align-items:center;gap:14px;
  }
  .brand__dot{width:34px;height:34px;border-radius:50%;background:var(--sky)}
  .brand__name{
    font-weight:700;font-size:38px;letter-spacing:1px;color:var(--navy);
  }

  .identity{
    position:absolute;left:56px;top:168px;
    display:flex;align-items:flex-start;gap:16px;
  }
  .person{text-align:right;white-space:nowrap}
  .person__name{
    font-family:"Oswald",sans-serif;font-weight:600;
    font-size:32px;line-height:1;color:var(--navy);letter-spacing:.5px;
  }
  .person__title{font-size:13px;color:var(--ink);margin-top:6px}

  .divider{width:1.5px;height:60px;background:var(--amber);flex:none}
  .contact{
    list-style:none;white-space:nowrap;
    font-size:12.5px;color:var(--ink);line-height:19px;margin-top:2px;
  }
  .contact li{display:flex;align-items:center;gap:6px}
  .contact svg{width:10px;height:10px;fill:var(--navy);flex:none}

  .back-pattern{position:absolute;inset:0;background:linear-gradient(135deg,#0b0b0c 0%,#1b1b1e 55%,#2a2a2d 100%)}
  .back-brand{
    position:absolute;right:40px;top:130px;display:flex;align-items:center;gap:8px;
  }
  .back-brand__dot{width:16px;height:16px;border-radius:50%;background:var(--sky)}
  .back-brand__name{font-weight:700;font-size:16px;color:var(--sky);letter-spacing:.5px}
</style>
</head>
<body>
  <section class="card card--front">
    <div class="brand">
      <span class="brand__dot"></span>
      <span class="brand__name">CREWWELL</span>
    </div>
    <div class="identity">
      <div class="person">
        <p class="person__name">DANIEL MORROW</p>
        <p class="person__title">Director</p>
      </div>
      <span class="divider"></span>
      <ul class="contact">
        <li><svg viewBox="0 0 10 10"><path d="M2 0h2l1 2.5-1.3 1a5 5 0 0 0 2.8 2.8l1-1.3L10 6v2a2 2 0 0 1-2 2A8 8 0 0 1 0 2a2 2 0 0 1 2-2z"/></svg>(555)014 2286</li>
        <li><svg viewBox="0 0 10 10"><path d="M0 2h10v6H0z"/><path d="M0 2l5 3.5L10 2" fill="none" stroke="#fff" stroke-width=".8"/></svg>info@crewwell.com</li>
        <li><svg viewBox="0 0 10 10"><circle cx="5" cy="5" r="5"/><path d="M0 5h10M5 0v10" stroke="#fff" stroke-width=".7"/></svg>www.crewwell.com</li>
      </ul>
    </div>
  </section>

  <section class="card card--back">
    <div class="back-pattern" role="img" aria-label="Repeating tonal brand pattern in glossy black on matte black"></div>
    <div class="back-brand">
      <span class="back-brand__dot"></span>
      <span class="back-brand__name">CREWWELL</span>
    </div>
  </section>
</body>
</html>
```